Business Card for a Creative Technology based HR services company

Our company name is Lumo8, and we build large communities of HR (human resource) and finance personnels through our mobile platform, and we conduct lots of on-line and off-line activities to get everyone constantly connected. Behind all these, we will also provide on-site HR and finance contractors to our clients, plus a host of other HR-related services. No process in our company takes more than 5-steps.
Our company slogan: Touching Your Future
Target Market(s)
All human resource (HR) and finance personnels, from new entrants to highly experienced senior professionals.
Industry/Entity Type
Finance
Colors
Designer to choose colors to be used in the design.
Look and feel
Each slider illustrates characteristics of the customer's brand and the style your logo design should communicate.

```html
<!DOCTYPE html>
<html lang="en">
<head>
<meta charset="utf-8">
<title>Lumo8 Business Card</title>
<link rel="stylesheet" href="https://fonts.googleapis.com/css2?family=Ubuntu:wght@400;500;700&display=swap">
<style>
  :root {
    --navy: #0d2a57;
    --red: #e8171f;
    --white: #ffffff;
    --ink: #3a3f4a;
    --backdrop: #ece9e4;
  }
  * { margin: 0; padding: 0; box-sizing: border-box; }
  html, body {
    width: 1073px;
    height: 1200px;
    overflow: hidden;
    background: var(--backdrop);
    font-family: "Ubuntu", sans-serif;
  }
  .stage {
    position: relative;
    width: 1073px;
    height: 1200px;
  }
  .card {
    position: absolute;
    top: 280px;
    width: 400px;
    height: 640px;
    background: var(--navy);
    box-shadow: 0 14px 34px rgba(0,0,0,0.22);
    overflow: hidden;
  }
  .card--front { left: 90px; }
  .card--back { left: 583px; }

  .card__face {
    position: absolute;
    top: 26px;
    left: 26px;
    right: 26px;
    bottom: 26px;
    background: var(--white);
    border-radius: 20px;
  }

  .brand {
    position: absolute;
    display: flex;
    align-items: center;
    gap: 8px;
  }
  .brand__name {
    font-weight: 700;
    color: var(--navy);
    letter-spacing: -1px;
    line-height: 1;
  }
  .brand__dot {
    border-radius: 50%;
    background: var(--red);
  }

  .card--front .brand {
    top: 50%;
    left: 50%;
    transform: translate(-50%, -50%);
  }
  .card--front .brand__name { font-size: 62px; }
  .card--front .brand__dot { width: 26px; height: 26px; }

  /* back */
  .card--back .card__face {
    right: 26px;
    border-radius: 6px;
  }
  .back__band {
    position: absolute;
    top: 0;
    right: 0;
    bottom: 0;
    width: 118px;
    background: var(--navy);
  }
  .back__stripe {
    position: absolute;
    top: 0;
    right: 118px;
    bottom: 0;
    width: 26px;
    background: var(--red);
  }
  .card--back .brand {
    top: 120px;
    left: 40px;
  }
  .card--back .brand__name { font-size: 44px; }
  .card--back .brand__dot { width: 18px; height: 18px; }

  .person {
    position: absolute;
    top: 50%;
    right: 59px;
    transform: translate(50%, -50%) rotate(90deg);
    white-space: nowrap;
    text-align: center;
  }
  .person__name {
    font-size: 34px;
    font-weight: 500;
    letter-spacing: 4px;
    color: var(--white);
    text-transform: uppercase;
  }
  .person__role {
    position: absolute;
    top: 50%;
    right: 131px;
    transform: translate(50%, -50%) rotate(90deg);
    font-size: 11px;
    letter-spacing: 3px;
    color: var(--white);
    text-transform: uppercase;
    white-space: nowrap;
  }

  .icons {
    position: absolute;
    bottom: 60px;
    right: 124px;
    display: flex;
    flex-direction: column;
    gap: 6px;
  }
  .icons__item {
    width: 14px;
    height: 14px;
    background: var(--white);
    border-radius: 2px;
  }

  .contact {
    position: absolute;
    left: 30px;
    bottom: 40px;
    transform-origin: left bottom;
    transform: translateX(100px) rotate(-90deg);
    list-style: none;
    font-size: 11px;
    line-height: 1.55;
    color: var(--ink);
    white-space: nowrap;
  }
</style>
</head>
<body>
<main class="stage">
  <section class="card card--front" aria-label="Card front">
    <div class="card__face">
      <div class="brand">
        <span class="brand__name">Lumo8</span>
        <span class="brand__dot"></span>
      </div>
    </div>
  </section>

  <section class="card card--back" aria-label="Card back">
    <div class="back__band"></div>
    <div class="back__stripe"></div>
    <div class="card__face" style="right:144px;">
      <div class="brand">
        <span class="brand__name">Lumo8</span>
        <span class="brand__dot"></span>
      </div>
      <ul class="contact">
        <li>012 345 6789</li>
        <li>012 345 6790</li>
        <li>dana@lumo8mail.com</li>
        <li>www.lumo8hr.com</li>
        <li>18 Harbor Road</li>
        <li>3rd Floor, Kestrel Building</li>
      </ul>
    </div>
    <div class="person"><span class="person__name">Dana Reyes</span></div>
    <div class="person__role">Creative Manager</div>
    <div class="icons">
      <span class="icons__item"></span>
      <span class="icons__item"></span>
      <span class="icons__item"></span>
    </div>
  </section>
</main>
</body>
</html>
```